Whitcombe Business Card Design

The name of the business is Dario Whitcombe, CPA LLC
The service that we offer is Accounting, Tax & Consulting Services. I need it to have the following items:
Dario Whitcombe, Principal
Phone Number
Email Address
Physical Address

I have attached the company logo, one in black and one in white. Please provide a design in black background and the other in white background. Please include "Accounting, Tax & Consulting Services". I want the business card to be clean and very professional.

```html
<!DOCTYPE html>
<html lang="en">
<head>
<meta charset="utf-8">
<title>Dario Whitcombe, CPA LLC – Business Card</title>
<link rel="stylesheet" href="https://fonts.googleapis.com/css2?family=Montserrat:wght@500;600&family=Roboto:wght@400;500;700&display=swap">
<style>
  :root {
    --backdrop: #d9d9d9;
    --card: #0e0e10;
    --red: #9b1b1e;
    --mark-grey: #4a4a4c;
    --title-grey: #a9a9a9;
    --label-grey: #b4b4b4;
    --value-grey: #a6a6a6;
    --rule: #3a3a3c;
    --white: #ffffff;
  }
  * { box-sizing: border-box; margin: 0; padding: 0; }
  html, body {
    width: 1200px; height: 900px; overflow: hidden;
    background: var(--backdrop);
  }
  .stage { position: relative; width: 1200px; height: 900px; }
  .card {
    position: absolute; left: 232px; width: 700px; height: 400px;
    background: var(--card); overflow: hidden;
  }
  .card--front { top: 42px; }
  .card--back { top: 460px; height: 401px; }

  /* Front */
  .front-square {
    position: absolute; left: 320px; top: 110px; width: 60px; height: 60px;
    background: var(--red);
  }
  .front-name {
    position: absolute; left: 0; right: 0; top: 238px; text-align: center;
    font-family: "Montserrat", sans-serif; font-weight: 600; font-size: 40px;
    color: var(--mark-grey); letter-spacing: 0.5px; white-space: nowrap;
  }
  .front-tagline {
    position: absolute; left: 0; right: 0; top: 292px; text-align: center;
    font-family: "Montserrat", sans-serif; font-weight: 600; font-size: 30px;
    color: var(--title-grey); letter-spacing: 3px; white-space: nowrap;
  }

  /* Back */
  .brand { position: absolute; left: 34px; top: 32px; display: flex; align-items: center; gap: 12px; }
  .brand-square { width: 40px; height: 40px; background: var(--red); }
  .brand-name {
    font-family: "Montserrat", sans-serif; font-weight: 500; font-size: 15px;
    color: var(--mark-grey); line-height: 1.2; white-space: nowrap;
  }
  .brand-tagline {
    font-family: "Montserrat", sans-serif; font-weight: 600; font-size: 11px;
    color: var(--title-grey); letter-spacing: 1.2px; white-space: nowrap;
  }
  .person { position: absolute; right: 27px; top: 30px; text-align: left; }
  .person-name {
    font-family: "Roboto", sans-serif; font-weight: 700; font-size: 29px;
    color: var(--title-grey); white-space: nowrap;
  }
  .person-title {
    font-family: "Roboto", sans-serif; font-weight: 500; font-size: 13px;
    color: var(--red); letter-spacing: 6px; margin-left: 3px;
  }
  .contact-rule {
    position: absolute; left: 76px; top: 157px; width: 1px; height: 180px;
    background: var(--rule);
  }
  .contact-row {
    position: absolute; left: 42px; display: flex; align-items: flex-start;
    font-family: "Roboto", sans-serif; font-size: 18px; white-space: nowrap;
  }
  .contact-icon { width: 24px; height: 24px; margin-right: 28px; flex: none; }
  .contact-label { width: 130px; color: var(--label-grey); font-weight: 500; }
  .contact-value { color: var(--value-grey); font-weight: 400; line-height: 1.3; }
  .band {
    position: absolute; left: 0; right: 0; bottom: 0; height: 48px;
    background: var(--red); display: flex; align-items: center; justify-content: center;
    font-family: "Roboto", sans-serif; font-weight: 700; font-size: 23px;
    color: var(--white); letter-spacing: 3.6px; white-space: nowrap;
  }
</style>
</head>
<body>
<div class="stage">

  <section class="card card--front">
    <div class="front-square"></div>
    <div class="front-name">Dario Whitcombe, CPA LLC</div>
    <div class="front-tagline">CERTIFIED PUBLIC ACCOUNTANT</div>
  </section>

  <section class="card card--back">
    <div class="brand">
      <div class="brand-square"></div>
      <div>
        <div class="brand-name">Dario Whitcombe, CPA LLC</div>
        <div class="brand-tagline">CERTIFIED PUBLIC ACCOUNTANT</div>
      </div>
    </div>

    <div class="person">
      <div class="person-name">Dario Whitcombe</div>
      <div class="person-title">PRINCIPAL</div>
    </div>

    <div class="contact-rule"></div>

    <div class="contact-row" style="top:173px">
      <svg class="contact-icon" viewBox="0 0 24 24" aria-hidden="true"><path fill="var(--red)" d="M6.6 10.8c1.4 2.8 3.8 5.1 6.6 6.6l2.2-2.2c.3-.3.7-.4 1-.2 1.1.4 2.3.6 3.6.6.6 0 1 .4 1 1V20c0 .6-.4 1-1 1C10.6 21 3 13.4 3 4c0-.6.4-1 1-1h3.5c.6 0 1 .4 1 1 0 1.3.2 2.5.6 3.6.1.3 0 .7-.2 1z"/></svg>
      <span class="contact-label">Office Phone</span>
      <span class="contact-value">: (555) 014-0372</span>
    </div>

    <div class="contact-row" style="top:207px">
      <svg class="contact-icon" viewBox="0 0 24 24" aria-hidden="true"><rect x="2" y="5" width="20" height="14" fill="var(--red)"/><path d="M2 5l10 8 10-8M2 19l7-7M22 19l-7-7" stroke="var(--card)" stroke-width="1.4" fill="none"/></svg>
      <span class="contact-label">Email ID</span>
      <span class="contact-value">: info@whitcombe.com</span>
    </div>

    <div class="contact-row" style="top:241px">
      <svg class="contact-icon" viewBox="0 0 24 24" aria-hidden="true"><path fill="var(--red)" d="M12 2a7 7 0 0 0-7 7c0 5 7 13 7 13s7-8 7-13a7 7 0 0 0-7-7zm0 9.5A2.5 2.5 0 1 1 12 6.5a2.5 2.5 0 0 1 0 5z"/></svg>
      <span class="contact-label">Address</span>
      <span class="contact-value">: 421, Address line goes here<br>&nbsp;&nbsp;45552, Country Name</span>
    </div>

    <div class="contact-row" style="top:293px">
      <svg class="contact-icon" viewBox="0 0 24 24" aria-hidden="true"><g fill="none" stroke="var(--red)" stroke-width="1.4"><circle cx="12" cy="12" r="10"/><ellipse cx="12" cy="12" rx="4.5" ry="10"/><path d="M2 12h20M4 7h16M4 17h16M12 2v20"/></g></svg>
      <span class="contact-label">Website</span>
      <span class="contact-value">: www.websitename.com</span>
    </div>

    <div class="band">ACCOUNTING, TAX &amp; CONSULTING SERVICES</div>
  </section>

</div>
</body>
</html>
```